Bookcover: Ways to Turn Into a Bold Pathfinder

I am publishing a super-low-cost innovation book for €4,99 on Quillmere Open Press to help everyone become a great innovator: young ambitious people without college education nor a big budget. Do you want to help me?

Brief:
Design a book cover 1600 x 2560 pixels for QOP.
Main title: Ways to Turn Into a Bold Pathfinder
Sub title: mindset - insights - skills & tools
Author: Joost ter Brakel
Design: captive, and appealing to everyone
Target Group: young ambitious people without college education

For quillmere please format the height/width ratio of 1.6:1

```html
<!DOCTYPE html>
<html lang="en">
<head>
<meta charset="utf-8">
<title>Ways to Turn Into a Bold Pathfinder – Book Cover</title>
<link rel="stylesheet" href="https://fonts.googleapis.com/css2?family=Bebas+Neue&family=Poppins:wght@600&display=swap">
<style>
  :root {
    --backdrop: #5f6670;
    --cover-sky: #d0dcef;
    --ink: #16161c;
    --title-violet: #776690;
    --night-navy: #1e1a4a;
    --accent-orange: #ff8a00;
    --white: #ffffff;
  }
  * { margin: 0; padding: 0; box-sizing: border-box; }
  html, body {
    width: 800px; height: 1200px; overflow: hidden;
    background: var(--backdrop);
  }
  .book-cover {
    position: absolute; left: 25px; top: 0;
    width: 750px; height: 1200px;
    background: var(--cover-sky);
    overflow: hidden;
  }
  .team-photo {
    position: absolute; left: 0; top: 430px;
    width: 750px; height: 770px;
    background:
      radial-gradient(ellipse 260px 220px at 390px 340px, rgba(235,245,255,0.85), rgba(235,245,255,0) 70%),
      linear-gradient(180deg,
        rgba(208,220,239,0) 0%,
        #a9bde0 18%,
        #8099c9 40%,
        #575d9a 62%,
        #2b2660 80%,
        var(--night-navy) 88%);
  }
  .kicker {
    position: absolute; left: 0; width: 100%;
    text-align: center;
    font-family: 'Poppins', sans-serif; font-weight: 600;
    font-size: 34px; line-height: 1;
    letter-spacing: 0.55em; text-indent: 0.55em;
    color: var(--ink);
  }
  .kicker--first { top: 86px; }
  .kicker--second { top: 124px; }
  .title-svg {
    position: absolute; left: 0; top: 0;
    width: 750px; height: 520px;
  }
  .title-svg text {
    font-family: 'Bebas Neue', sans-serif;
  }
  .subtitle {
    position: absolute; left: 0; top: 1000px; width: 100%;
    display: flex; justify-content: center; align-items: center;
    font-family: 'Poppins', sans-serif; font-weight: 600;
    font-size: 21px; letter-spacing: 0.14em;
    color: var(--white);
  }
  .subtitle .divider {
    width: 1px; height: 24px; margin: 0 26px;
    background: var(--accent-orange);
  }
  .author {
    position: absolute; left: 0; top: 1068px; width: 100%;
    text-align: center;
    font-family: 'Bebas Neue', sans-serif;
    font-size: 58px; line-height: 1;
    color: var(--accent-orange);
  }
</style>
</head>
<body>
  <main class="book-cover">
    <div class="team-photo" role="img" aria-label="Photo of a team stacking fists together in the centre, overlaid with glowing technology rings"></div>

    <p class="kicker kicker--first">WAYS TO</p>
    <p class="kicker kicker--second">TURN INTO A</p>

    <svg class="title-svg" viewBox="0 0 750 520" aria-label="Bold Pathfinder">
      <defs>
        <linearGradient id="skyline-fill" x1="0" y1="0" x2="1" y2="0.3">
          <stop offset="0" stop-color="#1d2a45"/>
          <stop offset="0.3" stop-color="#3a4d73"/>
          <stop offset="0.52" stop-color="#c8742f"/>
          <stop offset="0.68" stop-color="#d9431c"/>
          <stop offset="0.85" stop-color="#2a2326"/>
          <stop offset="1" stop-color="#141318"/>
        </linearGradient>
      </defs>
      <text x="375" y="379" text-anchor="middle" font-size="296"
            textLength="540" lengthAdjust="spacingAndGlyphs"
            fill="url(#skyline-fill)" role="img"
            aria-label="Title word filled with a photo of glass office towers at sunset">BOLD</text>
      <text x="375" y="504" text-anchor="middle" font-size="168"
            textLength="542" lengthAdjust="spacingAndGlyphs"
            fill="var(--title-violet)">PATHFINDER</text>
    </svg>

    <div class="subtitle">
      <span>MINDSET</span>
      <span class="divider"></span>
      <span>INSIGHTS</span>
      <span class="divider"></span>
      <span>SKILLS &amp; TOOLS</span>
    </div>

    <p class="author">JOOST TER BRAKEL</p>
  </main>
</body>
</html>
```